Graphic- Educational Visual

Brisko Dog Training has created an educational tool to help its students understand and prioritize some key concepts in their dog training.

We are requesting a visual of this tool be designed.

Name/title of tool (to be included in graphic): The Brisko Pathway
Description: Funnel (inverted pyramid).

From top to bottom, the levels are called:

Connect
Develop
Progress
Refine

The diagram should also include a cycle around it to, to represent that one is always moving through the levels.

Business colours are included below to make sure the funnel's colours complement the website colours or at least don't clash:

#0AA1C7 Blue and #7FC31B Green
Purple as a secondary colour -75279C

For reference, business logo is attached.

Dog Training

```html
<!DOCTYPE html>
<html lang="en">
<head>
<meta charset="utf-8">
<title>The Brisko Pathway – Funnel Graphic</title>
<link href="https://fonts.googleapis.com/css2?family=Fredoka:wght@600&family=Great+Vibes&display=swap" rel="stylesheet">
<style>
  :root {
    --brand-blue: #0AA1C7;
    --brand-green: #7FC31B;
    --brand-purple: #75279C;
    --stripe-blue: #1aa7d6;
    --stripe-green: #12c41a;
    --stripe-purple: #a21fb5;
    --level-connect: #8c0a70;
    --level-connect-dark: #5e0a4c;
    --level-develop: #9d63c4;
    --level-develop-dark: #6b3a8e;
    --level-progress: #3f93d4;
    --level-progress-dark: #1f5f9c;
    --level-refine: #86cf5a;
    --white: #ffffff;
    --page: #ffffff;
  }
  html, body {
    margin: 0;
    padding: 0;
    width: 1200px;
    height: 1000px;
    overflow: hidden;
    background: var(--page);
  }
  .canvas {
    position: relative;
    width: 1200px;
    height: 1000px;
  }
  .variant {
    position: absolute;
    top: 167px;
    width: 542px;
    height: 590px;
    box-shadow: 0 2px 8px rgba(0,0,0,0.18);
  }
  .variant--blue { left: 38px; }
  .variant--grey { left: 614px; }
  .variant svg { display: block; }
  .title-script {
    font-family: "Great Vibes", cursive;
    fill: var(--white);
  }
  .title-block, .level-label, .brand-name {
    font-family: "Fredoka", sans-serif;
    font-weight: 600;
  }
  .title-block { fill: var(--white); }
  .level-label { fill: var(--white); font-size: 34px; letter-spacing: 0.5px; }
  .brand-name { fill: var(--brand-blue); }
</style>
</head>
<body>
<main class="canvas">

  <section class="variant variant--blue" aria-label="The Brisko Pathway, blue colourway">
    <svg width="542" height="590" viewBox="0 0 542 590">
      <defs>
        <linearGradient id="bg-blue" x1="0" y1="0" x2="0" y2="1">
          <stop offset="0" stop-color="#00c6f0"/>
          <stop offset="0.5" stop-color="#0a8ee0"/>
          <stop offset="1" stop-color="#0a4fc0"/>
        </linearGradient>
        <linearGradient id="arrow-blue" x1="0" y1="0" x2="0" y2="1">
          <stop offset="0" stop-color="#3fd0f5"/>
          <stop offset="1" stop-color="#1466c8"/>
        </linearGradient>
        <linearGradient id="dog-tones-a" x1="0" y1="0" x2="1" y2="1">
          <stop offset="0" stop-color="#c56a2a"/>
          <stop offset="0.6" stop-color="#8a4a22"/>
          <stop offset="1" stop-color="#3a2418"/>
        </linearGradient>
      </defs>
      <rect class="panel-bg" width="542" height="590" fill="url(#bg-blue)"/>
      <rect class="stripe" x="0" y="0" width="155" height="8" fill="var(--stripe-blue)"/>
      <rect class="stripe" x="167" y="0" width="185" height="8" fill="var(--stripe-green)"/>
      <rect class="stripe" x="362" y="0" width="180" height="8" fill="var(--stripe-purple)"/>
      <line x1="0" y1="18" x2="542" y2="18" stroke="rgba(255,255,255,0.45)" stroke-dasharray="3 3"/>

      <text class="title-script" x="38" y="88" font-size="64">The</text>
      <text class="title-block" x="160" y="72" font-size="46" textLength="200" lengthAdjust="spacingAndGlyphs">BRISKO</text>
      <text class="title-block" x="150" y="125" font-size="64" textLength="312" lengthAdjust="spacingAndGlyphs">PATHWAY</text>

      <path class="cycle-ring" d="M 95 215 A 180 170 0 0 0 445 215" fill="none" stroke="rgba(255,255,255,0.18)" stroke-width="34"/>
      <path class="cycle-arrow" d="M 48 215 Q 40 350 118 408" fill="none" stroke="url(#arrow-blue)" stroke-width="16" stroke-linecap="round"/>
      <polygon points="100,385 140,420 95,428" fill="#1466c8"/>
      <path class="cycle-arrow" d="M 428 408 Q 500 345 493 240" fill="none" stroke="url(#arrow-blue)" stroke-width="16" stroke-linecap="round"/>
      <polygon points="476,250 494,218 512,252" fill="#3fd0f5"/>

      <polygon points="92,201 465,201 452,215 77,215" fill="var(--level-connect-dark)"/>
      <polygon points="44,138 497,138 465,201 92,201" fill="var(--level-connect)"/>
      <text class="level-label" x="100" y="182">CONNECT</text>
      <polygon points="120,276 420,276 399,293 124,293" fill="var(--level-develop-dark)"/>
      <polygon points="77,215 452,215 420,276 120,276" fill="var(--level-develop)"/>
      <text class="level-label" x="132" y="258">DEVELOP</text>
      <polygon points="162,355 372,355 344,373 177,373" fill="var(--level-progress-dark)"/>
      <polygon points="124,293 399,293 372,355 162,355" fill="var(--level-progress)"/>
      <text class="level-label" x="176" y="337">PROGRESS</text>
      <polygon points="177,373 344,373 306,436 224,436" fill="var(--level-refine)"/>
      <text class="level-label" x="208" y="415">REFINE</text>

      <path class="base-band" d="M0 485 Q 271 395 542 485 L542 590 L0 590 Z" fill="var(--white)"/>
      <path class="dog-photo" role="img" aria-label="Photo of a brown and tan dog's eyes and nose peeking up from the bottom edge" d="M0 493 Q 147 446 262 448 Q 292 450 300 478 Q 306 530 296 590 L0 590 Z" fill="url(#dog-tones-a)"/>
      <text class="brand-name" x="487" y="530" font-size="48" text-anchor="end">Brisko</text>
      <text class="brand-name" x="487" y="568" font-size="22" text-anchor="end">Dog Training</text>
    </svg>
  </section>

  <section class="variant variant--grey" aria-label="The Brisko Pathway, grey colourway">
    <svg width="542" height="590" viewBox="0 0 542 590">
      <defs>
        <linearGradient id="bg-grey" x1="0" y1="0" x2="0" y2="1">
          <stop offset="0" stop-color="#aab3ba"/>
          <stop offset="1" stop-color="#939ea8"/>
        </linearGradient>
        <linearGradient id="arrow-grey" x1="0" y1="0" x2="0" y2="1">
          <stop offset="0" stop-color="#d6e6f0"/>
          <stop offset="1" stop-color="#1d78c8"/>
        </linearGradient>
        <linearGradient id="dog-tones-b" x1="0" y1="0" x2="1" y2="1">
          <stop offset="0" stop-color="#c56a2a"/>
          <stop offset="0.6" stop-color="#8a4a22"/>
          <stop offset="1" stop-color="#3a2418"/>
        </linearGradient>
      </defs>
      <rect class="panel-bg" width="542" height="590" fill="url(#bg-grey)"/>
      <rect class="stripe" x="0" y="0" width="155" height="8" fill="var(--stripe-blue)"/>
      <rect class="stripe" x="167" y="0" width="185" height="8" fill="var(--stripe-green)"/>
      <rect class="stripe" x="362" y="0" width="180" height="8" fill="var(--stripe-purple)"/>
      <line x1="0" y1="18" x2="542" y2="18" stroke="rgba(255,255,255,0.45)" stroke-dasharray="3 3"/>

      <text class="title-script" x="38" y="88" font-size="64">The</text>
      <text class="title-block" x="160" y="72" font-size="46" textLength="200" lengthAdjust="spacingAndGlyphs">BRISKO</text>
      <text class="title-block" x="150" y="125" font-size="64" textLength="312" lengthAdjust="spacingAndGlyphs">PATHWAY</text>

      <path class="cycle-ring" d="M 95 215 A 180 170 0 0 0 445 215" fill="none" stroke="rgba(255,255,255,0.3)" stroke-width="34"/>
      <path class="cycle-arrow" d="M 48 215 Q 40 350 118 408" fill="none" stroke="url(#arrow-grey)" stroke-width="16" stroke-linecap="round"/>
      <polygon points="100,385 140,420 95,428" fill="#1d78c8"/>
      <path class="cycle-arrow" d="M 428 408 Q 500 345 493 240" fill="none" stroke="url(#arrow-grey)" stroke-width="16" stroke-linecap="round"/>
      <polygon points="476,250 494,218 512,252" fill="#d6e6f0"/>

      <polygon points="92,201 465,201 452,215 77,215" fill="var(--level-connect-dark)"/>
      <polygon points="44,138 497,138 465,201 92,201" fill="var(--level-connect)"/>
      <text class="level-label" x="100" y="182">CONNECT</text>
      <polygon points="120,276 420,276 399,293 124,293" fill="var(--level-develop-dark)"/>
      <polygon points="77,215 452,215 420,276 120,276" fill="var(--level-develop)"/>
      <text class="level-label" x="132" y="258">DEVELOP</text>
      <polygon points="162,355 372,355 344,373 177,373" fill="var(--level-progress-dark)"/>
      <polygon points="124,293 399,293 372,355 162,355" fill="var(--level-progress)"/>
      <text class="level-label" x="176" y="337">PROGRESS</text>
      <polygon points="177,373 344,373 306,436 224,436" fill="var(--level-refine)"/>
      <text class="level-label" x="208" y="415">REFINE</text>

      <path class="base-band" d="M0 485 Q 271 395 542 485 L542 590 L0 590 Z" fill="var(--white)"/>
      <path class="dog-photo" role="img" aria-label="Photo of a brown and tan dog's eyes and nose peeking up from the bottom edge" d="M0 493 Q 147 446 262 448 Q 292 450 300 478 Q 306 530 296 590 L0 590 Z" fill="url(#dog-tones-b)"/>
      <text class="brand-name" x="487" y="530" font-size="48" text-anchor="end">Brisko</text>
      <text class="brand-name" x="487" y="568" font-size="22" text-anchor="end">Dog Training</text>
    </svg>
  </section>

</main>
</body>
</html>
```